Business Card Design for Training Business

Clear Path Coaching is a new business that delivers training and other services with a focus on topics related to mental health and wellbeing, for example, Wellmind Response Course, Resilience etc. We have a strong focus on evidence-based psychology and neuroscience. I have a logo which I will upload with the brief, so please consider colours that work well with the logo.
Target Market(s)
Adults, workplaces (particularly government and not-for-profits)
Industry/Entity Type
Business
Contact Information for Business Card
Head Strong TrainingSamantha SellwoodDirector0438 770 850sam@headstrongtraining.com.auwww.headstrongtraining.com.au

```html
<!DOCTYPE html>
<html lang="en">
<head>
<meta charset="utf-8">
<title>Clear Path Coaching – Business Cards</title>
<link href="https://fonts.googleapis.com/css2?family=Questrial&display=swap" rel="stylesheet">
<style>
  :root {
    --teal: #23b3bd;
    --teal-soft: #7fd3cf;
    --mint: #cdeee6;
    --ink: #4a4644;
    --ink-soft: #8d8885;
    --paper: #ffffff;
    --backdrop: #ecedef;
  }
  * { box-sizing: border-box; margin: 0; padding: 0; }
  html, body {
    width: 1200px; height: 1197px; overflow: hidden;
    background: var(--backdrop);
    font-family: "Questrial", sans-serif;
    color: var(--ink);
  }
  .sheet {
    width: 1200px; height: 1197px;
    display: flex; flex-direction: column; align-items: center; justify-content: center;
    gap: 50px;
  }
  .card {
    position: relative; width: 860px; height: 526px;
    background: var(--paper); overflow: hidden;
    box-shadow: 0 6px 24px rgba(0,0,0,0.12);
  }
  .pattern-area { position: absolute; }
  .card-front .pattern-area { right: 0; top: 33px; width: 260px; height: 460px; }
  .card-back .pattern-area { left: 0; bottom: 16px; width: 380px; height: 300px; }

  .brand { position: absolute; display: flex; flex-direction: column; align-items: center; }
  .brand-mark { width: 74px; height: 74px; border-radius: 50%; background: var(--teal); opacity: .85; margin-bottom: 22px; }
  .brand-name {
    font-size: 24px; letter-spacing: 4px; text-transform: uppercase;
    color: var(--ink-soft); white-space: nowrap;
  }
  .card-front .brand { left: 56px; top: 46px; }

  .person { position: absolute; left: 56px; top: 248px; }
  .person-name { font-size: 27px; color: var(--ink); }
  .person-role { font-size: 16px; color: var(--ink-soft); margin-top: 6px; }

  .contacts { position: absolute; left: 56px; top: 334px; list-style: none; }
  .contacts li { display: flex; align-items: center; gap: 14px; font-size: 20px; color: var(--ink); height: 30px; }
  .contacts svg { width: 20px; height: 20px; flex: none; }

  .front-band { position: absolute; left: 0; bottom: 0; width: 860px; height: 64px; }
  .band-web {
    position: absolute; left: 56px; bottom: 12px;
    display: flex; align-items: center; gap: 14px;
    font-size: 19px; color: var(--paper); letter-spacing: .5px;
  }
  .band-web svg { width: 20px; height: 20px; }

  .card-back .brand { left: 0; right: 0; top: 200px; }
  .card-back .brand-name { font-size: 30px; letter-spacing: 6px; }
  .back-web {
    position: absolute; right: 40px; bottom: 40px;
    font-size: 17px; color: var(--ink-soft); letter-spacing: .5px;
  }
  .back-edge { position: absolute; left: 0; right: 0; bottom: 0; height: 16px; background: var(--teal); }
</style>
</head>
<body>
<main class="sheet">

  <section class="card card-front">
    <svg class="pattern-area" role="img" aria-label="Large geometric rosette decoration in teal and mint" viewBox="0 0 260 460">
      <defs>
        <radialGradient id="front-fill" cx="75%" cy="50%" r="80%">
          <stop offset="0" stop-color="#ffffff"/>
          <stop offset=".45" stop-color="#cdeee6"/>
          <stop offset="1" stop-color="#3bbcc3"/>
        </radialGradient>
      </defs>
      <circle cx="230" cy="230" r="230" fill="url(#front-fill)" opacity=".75"/>
    </svg>

    <div class="brand">
      <span class="brand-mark"></span>
      <span class="brand-name">Clear Path Coaching</span>
    </div>

    <div class="person">
      <p class="person-name">Rebecca Tanfield</p>
      <p class="person-role">Director</p>
    </div>

    <ul class="contacts">
      <li>
        <svg viewBox="0 0 20 20"><rect x="5" y="2" width="10" height="16" rx="2" fill="none" stroke="#23b3bd" stroke-width="2"/><rect x="7.5" y="5" width="5" height="4" fill="#23b3bd"/><circle cx="10" cy="14" r="1.3" fill="#23b3bd"/></svg>
        0491 362 517
      </li>
      <li>
        <svg viewBox="0 0 20 20"><rect x="1.5" y="4.5" width="17" height="11" fill="none" stroke="#23b3bd" stroke-width="2"/><path d="M2 5 L10 11 L18 5" fill="none" stroke="#23b3bd" stroke-width="2"/></svg>
        bec@clearpathcoaching.example.au
      </li>
    </ul>

    <svg class="front-band" viewBox="0 0 860 64" preserveAspectRatio="none" aria-hidden="true">
      <rect x="440" y="44" width="420" height="6" fill="#23b3bd"/>
      <path d="M0 20 H370 C410 20 430 30 452 64 H0 Z" fill="#23b3bd"/>
    </svg>
    <div class="band-web">
      <svg viewBox="0 0 20 20"><circle cx="10" cy="10" r="8.5" fill="none" stroke="#fff" stroke-width="1.8"/><path d="M1.5 10 H18.5 M10 1.5 C5 6 5 14 10 18.5 M10 1.5 C15 6 15 14 10 18.5" fill="none" stroke="#fff" stroke-width="1.4"/></svg>
      www.clearpathcoaching.example.au
    </div>
  </section>

  <section class="card card-back">
    <svg class="pattern-area" role="img" aria-label="Geometric rosette decoration rising from the lower corner" viewBox="0 0 380 300">
      <defs>
        <radialGradient id="back-fill" cx="50%" cy="100%" r="100%">
          <stop offset="0" stop-color="#ffffff"/>
          <stop offset=".4" stop-color="#cdeee6"/>
          <stop offset="1" stop-color="#3bbcc3"/>
        </radialGradient>
      </defs>
      <circle cx="170" cy="300" r="195" fill="url(#back-fill)" opacity=".75"/>
    </svg>

    <div class="brand">
      <span class="brand-name">Clear Path Coaching</span>
    </div>

    <p class="back-web">www.clearpathcoaching.example.au</p>
    <div class="back-edge"></div>
  </section>

</main>
</body>
</html>
```